Business Card Design for a Software Startup

We'd like to have a business card design. We already have a logo. Basically what we need is a clean design with name, address, cellphone and phone numbers, e-mail and web site address (front) and a space on the back with our logo with the company name on the right side and some texts on the bottom.
We are a development and consulting company in Brazil with highly qualified team of professionals in Java, iOS and Android development and consulting.

Target Market(s)

CIO, IT managers of mid to big size companies

Industry/Entity Type

Business

```html
<!DOCTYPE html>
<html lang="en">
<head>
<meta charset="utf-8">
<title>Quilvo Business Card</title>
<link rel="stylesheet" href="https://fonts.googleapis.com/css2?family=Jost:wght@400;500;600;700&display=swap">
<style>
  :root {
    --backdrop: #e9e9ee;
    --card: #ffffff;
    --navy: #0d3b66;
    --blue: #1a82c4;
    --ink: #3a3a3a;
    --muted: #5a5a5a;
  }
  * { box-sizing: border-box; margin: 0; padding: 0; }
  html, body { width: 1200px; height: 987px; overflow: hidden; }
  body {
    background: var(--backdrop);
    font-family: "Jost", sans-serif;
    position: relative;
  }
  .card {
    position: absolute;
    left: 250px;
    width: 700px;
    height: 400px;
    background: var(--card);
    border-radius: 40px;
    box-shadow: 0 6px 18px rgba(0,0,0,0.12);
    overflow: hidden;
  }
  .card--front { top: 60px; }
  .card--back { top: 527px; }

  /* Front */
  .accent-bar {
    position: absolute; left: 44px; top: 0;
    width: 10px; height: 46px; background: var(--navy);
  }
  .holder { position: absolute; left: 72px; top: 18px; }
  .holder__name { color: var(--navy); font-weight: 700; font-size: 30px; line-height: 1.1; }
  .holder__title { color: var(--muted); font-size: 20px; }
  .address {
    position: absolute; left: 72px; top: 118px;
    color: var(--ink); font-size: 20px; line-height: 1.3;
  }
  .contact {
    position: absolute; left: 72px; top: 196px;
    list-style: none; color: var(--ink); font-size: 20px; line-height: 1.35;
  }
  .contact__label { color: var(--blue); display: inline-block; width: 28px; }
  .website {
    position: absolute; left: 72px; top: 300px;
    color: var(--ink); font-size: 18px; letter-spacing: 6px;
  }
  .website b { color: var(--blue); font-weight: 400; }
  .brand {
    position: absolute; right: 52px; bottom: 48px;
    display: flex; align-items: center; gap: 14px;
  }
  .brand__mark { width: 38px; height: 38px; background: var(--blue); }
  .brand__name {
    color: var(--navy); font-weight: 600; font-size: 52px; letter-spacing: 2px;
  }

  /* Back */
  .back-brand {
    position: absolute; left: 0; right: 0; top: 120px;
    text-align: center; color: var(--navy);
    font-weight: 600; font-size: 110px; letter-spacing: 6px; line-height: 1;
  }
  .back-web {
    position: absolute; left: 0; right: 0; top: 270px;
    text-align: center; color: var(--muted);
    font-size: 24px; letter-spacing: 10px; font-weight: 500;
  }
</style>
</head>
<body>
  <section class="card card--front">
    <div class="accent-bar"></div>
    <div class="holder">
      <p class="holder__name">Your Name</p>
      <p class="holder__title">Title</p>
    </div>
    <p class="address">Door No. Street Name<br>City Name, State, Zip Code</p>
    <ul class="contact">
      <li><span class="contact__label">P:</span>123-456-7890</li>
      <li><span class="contact__label">C:</span>123-456-7890</li>
      <li><span class="contact__label">E:</span>yourname@quilvo.com</li>
    </ul>
    <p class="website">www.<b>quilvo</b>.com</p>
    <div class="brand">
      <span class="brand__mark"></span>
      <span class="brand__name">QUILVO</span>
    </div>
  </section>

  <section class="card card--back">
    <p class="back-brand">QUILVO</p>
    <p class="back-web">www.quilvo.com</p>
  </section>
</body>
</html>
```